Building company buisness cards

We are looking for a sharp modern new look for our business cards.We are a New Zealand based company that specialises in house and land packages.We have attached a photo of the current logo and would like to see if it can be improved somehow if needed.We are open to any colours but we have chosen Black and White at this stage. Feel free to change the font and make the logo smarter looking.Play with the colours and see what looks best.We want a card that looks so good know one will want to throw it away!

Target Market(s)

Building profesonals, home buyers

Industry/Entity Type

Building

Contact Information for Business Card

Garrick Tenwood
0275390628
garrickt@hartvale.co.nz

Font styles to use
Serif
Sans Serif

Colors

Designer to choose colors to be used in the design.

Requirements
Must have
• Just the logo on one side and details on the other
• Clean simple looking card
Nice to have
• Round corners and detail like raised or spot UV
• Something that stands out
Should not have
• To title needed, Director etc

```html
<!DOCTYPE html>
<html lang="en">
<head>
<meta charset="utf-8">
<title>Hartvale business cards</title>
<link href="https://fonts.googleapis.com/css2?family=Open+Sans:wght@400;700&display=swap" rel="stylesheet">
<style>
  :root {
    --backdrop: #2a2a2c;
    --card: #161617;
    --card-edge: #232325;
    --ink: #f4f4f4;
    --silver: #cfcfd2;
    --divider: #5a5a5e;
  }
  * { margin: 0; padding: 0; box-sizing: border-box; }
  html, body {
    width: 1200px; height: 885px; overflow: hidden;
    background: var(--backdrop);
  }
  .canvas { position: relative; width: 1200px; height: 885px; }
  .card {
    position: absolute;
    width: 500px; height: 290px;
    background: var(--card);
    border: 1px solid var(--card-edge);
    border-radius: 22px;
    box-shadow: 0 18px 40px rgba(0,0,0,.45);
  }
  .card--front { left: 90px; top: 140px; }
  .card--back { left: 610px; top: 455px; }

  /* front */
  .front-name {
    position: absolute; left: 0; right: 0; top: 96px;
    text-align: center;
    font-family: "Open Sans", Arial, sans-serif;
    font-weight: 700; font-size: 40px; line-height: 50px;
    color: var(--silver);
  }
  .front-web {
    position: absolute; left: 0; right: 0; bottom: 52px;
    text-align: center;
    font-family: "Open Sans", Arial, sans-serif;
    font-size: 13px; letter-spacing: 6px; color: var(--ink);
  }

  /* back */
  .brand-name {
    position: absolute; left: 34px; top: 122px;
    font-family: "Open Sans", Arial, sans-serif;
    font-weight: 700; font-size: 36px; line-height: 44px;
    color: var(--ink);
  }
  .divider {
    position: absolute; left: 288px; top: 58px;
    width: 1px; height: 120px;
    background: linear-gradient(var(--divider), transparent);
  }
  .details {
    position: absolute; left: 308px; top: 56px;
    font-family: "Open Sans", Arial, sans-serif; color: var(--ink);
  }
  .details__name { font-weight: 700; font-size: 16px; margin-bottom: 8px; }
  .details__line {
    display: flex; align-items: center; gap: 7px;
    font-size: 13px; line-height: 19px;
  }
  .details__line svg { width: 12px; height: 12px; flex: none; }
</style>
</head>
<body>
<div class="canvas">
  <section class="card card--front">
    <p class="front-name">Hartvale</p>
    <p class="front-web">www.Hartvale.co.nz</p>
  </section>

  <section class="card card--back">
    <p class="brand-name">Hartvale</p>
    <div class="divider"></div>
    <div class="details">
      <p class="details__name">Garrick Tenwood</p>
      <p class="details__line">
        <svg viewBox="0 0 12 12" aria-hidden="true"><path fill="#f4f4f4" d="M2.5 1h2l1 3-1.3 1a6 6 0 0 0 2.8 2.8l1-1.3 3 1v2a1 1 0 0 1-1 1A9.5 9.5 0 0 1 1.5 2a1 1 0 0 1 1-1z"/></svg>
        0275390628
      </p>
      <p class="details__line">
        <svg viewBox="0 0 12 12" aria-hidden="true"><rect x="1" y="2.5" width="10" height="7" fill="#f4f4f4"/><path d="M1 2.5 6 6.5 11 2.5" fill="none" stroke="#161617" stroke-width="1"/></svg>
        garrickt@hartvale.co.nz
      </p>
      <p class="details__line">
        <svg viewBox="0 0 12 12" aria-hidden="true"><circle cx="6" cy="6" r="5" fill="#f4f4f4"/><path d="M1 6h10M6 1c-2.2 2.8-2.2 7.2 0 10M6 1c2.2 2.8 2.2 7.2 0 10" fill="none" stroke="#161617" stroke-width=".9"/></svg>
        www.hartvale.co.nz
      </p>
    </div>
  </section>
</div>
</body>
</html>
```